Ridgeline Journeys business card

please see website
www.ridgelinejourneys.comau

info needed on card
Curtis Halvey
Ph
email
Adventure Riding GPS trails

please use my logo and colours off my site

Curtis Halvey
curtis@ridgelinejourneys.com

```html
<!DOCTYPE html>
<html lang="en">
<head>
<meta charset="utf-8">
<title>Ridgeline Journeys – Business Card</title>
<link rel="stylesheet" href="https://fonts.googleapis.com/css2?family=Arimo:wght@400;700&display=swap">
<style>
  :root {
    --page-bg: #e9e7e3;
    --card-white: #ffffff;
    --card-grey: #e4e4e4;
    --ink: #1a1a1a;
    --ink-soft: #555555;
    --accent-yellow: #f2e21c;
    --band-black: #0d0d0d;
    --band-text: #f4f4f4;
  }
  * { margin: 0; padding: 0; box-sizing: border-box; }
  html, body {
    width: 1200px; height: 902px; overflow: hidden;
    background: var(--page-bg);
    font-family: "Arimo", Arial, sans-serif;
  }
  .canvas { position: relative; width: 1200px; height: 902px; }
  .card {
    position: absolute; left: 250px;
    width: 700px; height: 400px;
    overflow: hidden;
    background: radial-gradient(ellipse at 60% 30%, var(--card-white) 0%, var(--card-grey) 100%);
    box-shadow: 0 6px 18px rgba(0,0,0,0.18);
  }
  .card--front { top: 34px; }
  .card--back { top: 468px; }

  .brand {
    position: absolute;
    display: flex; align-items: center; gap: 18px;
  }
  .brand__dot {
    width: 46px; height: 46px; border-radius: 50%;
    background: var(--accent-yellow);
    flex: none;
  }
  .brand__text { display: flex; flex-direction: column; }
  .brand__name {
    color: var(--ink);
    font-weight: 700;
    text-transform: uppercase;
    line-height: 0.95;
    letter-spacing: 0.01em;
  }
  .brand__tagline {
    margin-top: 12px;
    color: var(--ink-soft);
    font-size: 17px;
    font-weight: 400;
    letter-spacing: 0.12em;
    text-transform: uppercase;
  }
  .card--front .brand { left: 150px; top: 130px; }
  .card--front .brand__name { font-size: 52px; }
  .card--front .brand__dot { width: 70px; height: 70px; }

  .card--back .brand { left: 200px; top: 42px; }
  .card--back .brand__name { font-size: 40px; }

  .back-shapes { position: absolute; inset: 0; }

  .holder {
    position: absolute; left: 40px; top: 318px;
    color: var(--band-text);
    font-size: 36px; font-weight: 700;
  }
  .divider {
    position: absolute; left: 318px; top: 282px;
    width: 1px; height: 100px; background: var(--band-text);
  }
  .contact {
    position: absolute; left: 336px; top: 280px;
    list-style: none;
    color: var(--band-text);
    font-size: 18px;
  }
  .contact__item { display: flex; align-items: center; gap: 12px; height: 34px; }
  .contact__icon { width: 20px; height: 20px; flex: none; }
</style>
</head>
<body>
<main class="canvas">

  <section class="card card--front" aria-label="Card front">
    <div class="brand">
      <span class="brand__dot"></span>
      <div class="brand__text">
        <span class="brand__name">Ridgeline<br>Journeys</span>
        <span class="brand__tagline">Adventure Riding GPS Trails</span>
      </div>
    </div>
  </section>

  <section class="card card--back" aria-label="Card back">
    <svg class="back-shapes" width="700" height="400" viewBox="0 0 700 400" aria-hidden="true">
      <polygon points="0,250 120,250 640,168 690,108 700,108 700,400 0,400" fill="var(--band-black)"/>
      <polygon points="20,240 120,240 636,158 684,98 690,98 642,164 122,246 20,246" fill="var(--accent-yellow)"/>
    </svg>

    <div class="brand">
      <span class="brand__dot"></span>
      <span class="brand__name">Ridgeline<br>Journeys</span>
    </div>

    <p class="holder">Curtis Halvey</p>
    <span class="divider"></span>
    <ul class="contact">
      <li class="contact__item">
        <svg class="contact__icon" viewBox="0 0 20 20" aria-hidden="true">
          <path d="M5 2h3l1.5 4-2 1.5a10 10 0 0 0 5 5l1.5-2 4 1.5v3a2 2 0 0 1-2 2A15 15 0 0 1 3 4a2 2 0 0 1 2-2z" fill="none" stroke="var(--band-text)" stroke-width="1.5" stroke-linejoin="round"/>
        </svg>
        <span>Ph 0491 570 156</span>
      </li>
      <li class="contact__item">
        <svg class="contact__icon" viewBox="0 0 20 20" aria-hidden="true">
          <rect x="1" y="4" width="18" height="12" fill="none" stroke="var(--band-text)" stroke-width="1.6"/>
          <polyline points="1,4 10,11 19,4" fill="none" stroke="var(--band-text)" stroke-width="1.6"/>
        </svg>
        <span>curtis@ridgelinejourneys.com</span>
      </li>
      <li class="contact__item">
        <svg class="contact__icon" viewBox="0 0 20 20" aria-hidden="true">
          <circle cx="10" cy="10" r="8.5" fill="none" stroke="var(--band-text)" stroke-width="1.6"/>
          <ellipse cx="10" cy="10" rx="3.8" ry="8.5" fill="none" stroke="var(--band-text)" stroke-width="1.3"/>
          <line x1="1.5" y1="10" x2="18.5" y2="10" stroke="var(--band-text)" stroke-width="1.3"/>
        </svg>
        <span>www.ridgelinejourneys.comau</span>
      </li>
    </ul>
  </section>

</main>
</body>
</html>
```